Business Card Design - Amberfield Court

We are looking at a new design for our business cards that has a modern and professional look. We run a residential aged care facility focussing on the care of residents. The cards will be used for potential clients, consultants and business opportunities in this sector. Blue and white is our main colours and would to see these colours incorporated in the design.
Industry/Entity Type
Business
Contact Information for Business Card
Amberfield Court, Darren Walsh, dwalsh@amberfieldcourt.com.au, Finance Manager, 0472 639 208, BCom, 37 Marrabel Crescent, Brindle Vale, Qld 4093.
Look and feel
Each slider illustrates characteristics of the customer's brand and the style your logo design should communicate.

```html
<!DOCTYPE html>
<html lang="en">
<head>
<meta charset="utf-8">
<title>Amberfield Court – Business Card</title>
<link rel="stylesheet" href="https://fonts.googleapis.com/css2?family=Oswald:wght@300;400&family=Open+Sans:ital,wght@0,400;1,400&display=swap">
<style>
  :root {
    --brand-blue: #4d7a95;
    --brand-taupe: #a39b94;
    --ink: #3a3a3a;
    --card-white: #ffffff;
    --backdrop: #e6e6e4;
  }
  * { margin: 0; padding: 0; box-sizing: border-box; }
  html, body { width: 1200px; height: 1000px; overflow: hidden; background: var(--backdrop); }
  .canvas { position: relative; width: 1200px; height: 1000px; }
  .card {
    position: absolute; left: 236px; width: 728px; height: 416px; overflow: hidden;
  }
  .card--front { top: 72px; background: var(--brand-blue); }
  .card--back { top: 512px; background: var(--card-white); }

  .front-mark {
    position: absolute; left: 0; right: 0; top: 150px; text-align: center;
    font-family: "Oswald", sans-serif; font-weight: 300; font-size: 48px;
    letter-spacing: 3px; text-transform: uppercase; color: var(--card-white);
  }
  .front-url {
    position: absolute; left: 0; right: 0; top: 354px; text-align: center;
    font-family: "Open Sans", sans-serif; font-style: italic; font-size: 15px; color: var(--card-white);
  }

  .brand {
    position: absolute; left: 60px; top: 176px; width: 275px; text-align: center;
  }
  .brand-dot {
    display: block; width: 26px; height: 26px; margin: 0 auto 14px;
    border-radius: 50%; background: var(--brand-blue);
  }
  .brand-name {
    font-family: "Oswald", sans-serif; font-weight: 300; font-size: 27px;
    letter-spacing: 2px; text-transform: uppercase; color: var(--brand-blue); line-height: 1;
  }
  .brand-tagline {
    margin-top: 10px; font-family: "Open Sans", sans-serif; font-style: italic;
    font-size: 14px; color: var(--brand-taupe);
  }

  .contact { position: absolute; left: 381px; top: 86px; font-family: "Open Sans", sans-serif; color: var(--ink); }
  .contact-name {
    font-family: "Oswald", sans-serif; font-weight: 400; font-size: 21px;
    letter-spacing: 0.5px; text-transform: uppercase; color: var(--brand-blue); line-height: 1.1;
  }
  .contact-role { font-size: 15px; margin-top: 4px; }
  .contact-rule {
    width: 78px; height: 1px; margin: 10px 0 12px;
    background: linear-gradient(90deg, var(--brand-taupe), transparent);
  }
  .contact-address { font-size: 15px; line-height: 21px; }
  .contact-list { list-style: none; margin-top: 8px; font-size: 15px; line-height: 23px; }
  .contact-list li { display: flex; align-items: center; gap: 8px; }
  .contact-list svg { width: 12px; height: 12px; fill: var(--brand-blue); flex: none; }

  .card-wave { position: absolute; left: 0; bottom: 0; width: 728px; height: 120px; }
</style>
</head>
<body>
<main class="canvas">
  <section class="card card--front">
    <div class="front-mark">Amberfield Court</div>
    <div class="front-url">www.amberfieldcourt.com.au</div>
  </section>

  <section class="card card--back">
    <div class="brand">
      <span class="brand-dot"></span>
      <div class="brand-name">Amberfield Court</div>
      <div class="brand-tagline">Warmth, Respect, Independence</div>
    </div>

    <div class="contact">
      <div class="contact-name">Darren Walsh</div>
      <div class="contact-role">Finance Manager</div>
      <div class="contact-rule"></div>
      <div class="contact-address">37 Marrabel Crescent,<br>Brindle Vale, Qld 4093</div>
      <ul class="contact-list">
        <li><svg viewBox="0 0 12 12"><path d="M2.5 0.5l2 2.3-1.2 1.6c.7 1.6 2 2.9 3.6 3.6l1.6-1.2 2.3 2-1.3 2.2C5.6 11 1 6.4.3 2z"/></svg>0472 639 208</li>
        <li><svg viewBox="0 0 12 12"><path d="M0 2h12v8H0z M0 2l6 4.5L12 2" fill="none" stroke="#4d7a95" stroke-width="1.4"/></svg>dwalsh@amberfieldcourt.com.au</li>
        <li><svg viewBox="0 0 12 12"><g fill="none" stroke="#4d7a95" stroke-width="1"><circle cx="6" cy="6" r="5.3"/><ellipse cx="6" cy="6" rx="2.3" ry="5.3"/><path d="M.7 6h10.6M1.5 3.4h9M1.5 8.6h9"/></g></svg>www.amberfieldcourt.com.au</li>
      </ul>
    </div>

    <svg class="card-wave" viewBox="0 0 728 120" preserveAspectRatio="none">
      <path d="M0 30 C40 62 140 76 330 78 C200 80 60 72 0 52 Z" fill="var(--brand-taupe)"/>
      <path d="M0 60 C120 100 420 90 728 12 L728 120 L0 120 Z" fill="var(--brand-blue)"/>
    </svg>
  </section>
</main>
</body>
</html>
```